Copperleaf Roofing Business Card

This is my current business card. But I’d like to make some changes. Somewhere on the card I’d like to list some of the services we offer. Maybe on the back? But I’d still like to keep the red. White and black modern look.

-residential & commercial roofing
-Roof Repairs & Maintenance
-Storm Damage & Insurance Claims specialist
-Christmas Lights and permanent Christmas lights
Fencing. Windows. Gutters. Siding. Sheetrock, painting.

```html
<!DOCTYPE html>
<html lang="en">
<head>
<meta charset="utf-8">
<title>Copperleaf Roofing Co. – Business Card</title>
<link rel="stylesheet" href="https://fonts.googleapis.com/css2?family=Audiowide&family=Open+Sans:wght@400;600&display=swap">
<style>
  :root {
    --red: #e0202a;
    --red-deep: #8e0c12;
    --red-dark: #5e070b;
    --black: #111111;
    --white: #ffffff;
    --paper: #f3f3f3;
    --ink-soft: #444444;
    --backdrop: #d9d9d9;
  }
  * { box-sizing: border-box; margin: 0; padding: 0; }
  html, body { width: 1200px; height: 900px; overflow: hidden; }
  body {
    background: var(--backdrop);
    font-family: "Open Sans", sans-serif;
    display: flex;
    flex-direction: column;
    align-items: center;
    justify-content: center;
    gap: 24px;
  }
  .card {
    position: relative;
    width: 700px;
    height: 400px;
    border-radius: 28px;
    overflow: hidden;
    box-shadow: 0 8px 24px rgba(0,0,0,0.25);
  }

  /* Back: services */
  .card-back { color: var(--white); }
  .tartan-field {
    position: absolute; inset: 0;
    background: linear-gradient(135deg, var(--red-deep) 0%, var(--red) 35%, var(--red-dark) 60%, var(--red) 85%, var(--red-deep) 100%);
  }
  .back-content {
    position: relative;
    height: 100%;
    display: flex;
    flex-direction: column;
    align-items: center;
    justify-content: center;
    text-align: center;
    padding: 0 40px;
  }
  .brand {
    display: flex;
    align-items: center;
    gap: 14px;
    font-family: "Audiowide", sans-serif;
    font-size: 30px;
    letter-spacing: 1px;
    line-height: 1;
  }
  .brand-dot {
    width: 34px; height: 34px;
    border-radius: 50%;
    flex: none;
  }
  .card-back .brand { color: var(--white); margin-bottom: 26px; }
  .card-back .brand-dot { background: var(--black); }
  .services-title {
    font-size: 26px;
    font-weight: 600;
    letter-spacing: 1px;
    margin-bottom: 8px;
  }
  .services-list { list-style: none; font-size: 18px; font-weight: 600; line-height: 1.5; }

  /* Front: contact */
  .card-front { background: linear-gradient(120deg, var(--white) 0%, var(--paper) 100%); }
  .tartan-edge {
    position: absolute; inset: 0;
    background: linear-gradient(135deg, var(--red) 0%, var(--red-dark) 100%);
    clip-path: polygon(100% 72%, 100% 100%, 38% 100%, 38% 96%);
  }
  .front-content {
    position: relative;
    height: 100%;
    display: flex;
    flex-direction: column;
    align-items: center;
    padding-top: 90px;
  }
  .card-front .brand { color: var(--red); font-size: 34px; }
  .card-front .brand-dot { background: var(--red); width: 40px; height: 40px; }
  .contact-row {
    display: flex;
    align-items: center;
    margin-top: 60px;
    gap: 24px;
  }
  .person { text-align: right; font-family: "Audiowide", sans-serif; }
  .person-name { font-size: 30px; line-height: 1; }
  .person-name .first { color: var(--red); }
  .person-name .last { color: var(--black); }
  .person-role { font-family: "Open Sans", sans-serif; font-size: 16px; color: var(--red); margin-top: 4px; }
  .divider { width: 1px; height: 80px; background: #bbbbbb; }
  .contact-list { list-style: none; font-size: 16px; color: var(--ink-soft); line-height: 1.7; }
  .contact-list li { display: flex; align-items: center; gap: 10px; }
  .contact-list svg { width: 16px; height: 16px; flex: none; }
</style>
</head>
<body>

<section class="card card-back">
  <div class="tartan-field" role="img" aria-label="Red, black and white tartan pattern"></div>
  <div class="back-content">
    <div class="brand"><span class="brand-dot"></span>COPPERLEAF ROOFING CO.</div>
    <h2 class="services-title">SERVICES</h2>
    <ul class="services-list">
      <li>Residential &amp; Commercial Roofing | Roof Repairs &amp; Maintenance</li>
      <li>Storm Damage &amp; Insurance Claims Specialist</li>
      <li>Christmas Lights And Permanent Christmas Lights</li>
      <li>Fencing. Windows. Gutters. Siding. Sheetrock, painting.</li>
    </ul>
  </div>
</section>

<section class="card card-front">
  <div class="tartan-edge" role="img" aria-label="Red and black tartan band along the lower edge"></div>
  <div class="front-content">
    <div class="brand"><span class="brand-dot"></span>COPPERLEAF ROOFING CO.</div>
    <div class="contact-row">
      <div class="person">
        <div class="person-name"><span class="first">DALE</span> <span class="last">BRENNER</span></div>
        <div class="person-role">OWNER</div>
      </div>
      <div class="divider"></div>
      <ul class="contact-list">
        <li>
          <svg viewBox="0 0 16 16" aria-hidden="true"><path fill="#e0202a" d="M3.5 1.5l2.5 0 1 3.5-1.6 1.2a8 8 0 0 0 4.4 4.4L11 9l3.5 1v2.5c0 1-1 2-2 2A11 11 0 0 1 1.5 3.5c0-1 1-2 2-2z"/></svg>
          555-014-2291
        </li>
        <li>
          <svg viewBox="0 0 16 16" aria-hidden="true"><rect x="1" y="3" width="14" height="10" fill="#e0202a"/><path d="M1 3l7 6 7-6" fill="none" stroke="#fff" stroke-width="1.4"/></svg>
          dale@copperleafroofing.co
        </li>
        <li>
          <svg viewBox="0 0 16 16" aria-hidden="true"><g fill="none" stroke="#e0202a" stroke-width="1.3"><circle cx="8" cy="8" r="6.5"/><ellipse cx="8" cy="8" rx="3" ry="6.5"/><path d="M1.5 8h13"/></g></svg>
          www.copperleafroofing.co
        </li>
      </ul>
    </div>
  </div>
</section>

</body>
</html>
```